BrivoNest Learning App for Children with Dyslexia

Project Description:

We are seeking a talented UI/UX designer to create engaging and intuitive designs for Brivonest, an innovative educational app designed to help children learn letters and words through a multisensory learning approach. The app aims to be particularly helpful for children with dyslexia, providing a supportive and interactive learning environment.

Key App Features & Design Requirements:

Account Creation Screen: Design a welcoming and straightforward sign-up page that allows users to register with their email or continue with Quarnix. The design should be clean, focusing on user-friendliness and accessibility, adhering to our terms of service and privacy policy.

Main Screen Design: The main screen should allocate at least 4/6 of its height to the interactive drawing area. It needs to display word prompts in both correct and scrambled orders and include options to "Show all Words," "Play all words," and a search function. The interface should be vibrant, engaging, and easy to navigate for children.

Profile Section: Create a user-friendly profile page that allows users to edit their profile image, name, username, email, links, and bio. The design should be clean and encourage user engagement.

BrivoTally Page: This section will display the user's learning progress, including rankings, a learning curve, and recently learned words. It should visually represent progress in a motivating and understandable way, suitable for a younger audience.

Visual and Auditory Feedback Implementation: Incorporate elements that support visual and auditory feedback, using dyslexia-friendly formats. This includes choosing appropriate colors, fonts, and auditory cues.

Accessibility and Customization Settings: Designs should include settings for adjusting visual contrast, font size, and the word list to accommodate individual preferences and needs.

Feel free to add more interactions and/or pages.

Design preferences:

Color Scheme: Use a bright, inviting color palette that stimulates learning and engagement without overwhelming the users.
Font Selection: Opt for fonts that are readable and accessible, particularly for users with dyslexia.
Icons and Graphics: Design custom icons and graphics that are cohesive with the app's theme and purpose. Illustrations should be simple, relatable, and supportive of the learning process.

Target Market(s)

Educational

Industry/Entity Type

Educational

Colors
0054AA
0677BA
7BADD7
CADEEF
E8F1F8
0094D4
00A9DD
6FCCEA
C7EBF8
E9F6FB

Requirements
Must have
• Educational app, a writing area, scoring and account management
Nice to have
• Statistics, Ranking Page, Settings and some nice visual features

```html
<!DOCTYPE html>
<html lang="en">
<head>
<meta charset="UTF-8">
<title>Brivonest – App Screens</title>
<link href="https://fonts.googleapis.com/css2?family=Montserrat:wght@400;500;600;700&display=swap" rel="stylesheet">
<style>
:root{
  --blue-deep:#0054AA;
  --blue-mid:#0677BA;
  --blue-soft:#7BADD7;
  --blue-pale:#CADEEF;
  --blue-mist:#E8F1F8;
  --cyan:#0094D4;
  --cyan-bright:#00A9DD;
  --cyan-soft:#6FCCEA;
  --chip:#DEDEDE;
  --ink:#222;
  --ink-soft:#444;
  --rule:#555;
  --white:#fff;
  --page:#fff;
}
*{margin:0;padding:0;box-sizing:border-box}
html,body{width:1200px;height:796px;overflow:hidden;background:var(--page)}
body{font-family:'Montserrat',sans-serif;position:relative;color:var(--ink)}
.screen{position:absolute;top:36px;width:328px;height:720px;background:var(--white);border-radius:34px;overflow:hidden;box-shadow:0 0 0 1px #e2e2e2}
.screen--signup{left:38px}
.screen--main{left:442px}
.screen--profile{left:840px}
.abs{position:absolute}
.status{position:absolute;top:40px;left:26px;right:28px;display:flex;justify-content:space-between;align-items:center;font-size:14px;color:var(--ink)}
.status svg{display:block}
.center-x{left:0;right:0;text-align:center}

/* signup */
.brand{top:86px;font-size:32px;font-weight:700;color:var(--blue-deep);letter-spacing:-.5px}
.tagline{top:128px;font-size:13.5px;color:var(--cyan);font-weight:500}
.hero-art{left:78px;top:172px;width:192px;height:128px;border-radius:14px;background:linear-gradient(135deg,var(--blue-pale),var(--cyan-soft) 60%,var(--blue-mid))}
.signup-panel{left:0;right:0;top:336px;bottom:0;background:var(--blue-deep);border-top-left-radius:44px;color:var(--white)}
.signup-panel .title{top:50px;font-size:16px;font-weight:600}
.signup-panel .lead{top:84px;font-size:13.5px;font-weight:500;line-height:34px}
.email-field{left:22px;top:166px;width:284px;height:39px;border:1px solid var(--white);display:flex}
.email-field .value{flex:1;font-size:10.5px;display:flex;align-items:center;padding-left:12px;font-weight:500}
.email-field .btn{width:94px;background:var(--cyan-bright);display:flex;align-items:center;justify-content:center;font-size:14px;font-weight:500}
.alt-login{top:236px;display:flex;justify-content:center;align-items:center;gap:12px;font-size:11px;font-weight:500}
.alt-login .dash{width:30px;height:1px;background:var(--white)}
.alt-login .mark{width:12px;height:12px;border-radius:50%;background:var(--cyan-soft)}
.panel-rule{left:0;right:0;top:278px;height:1px;background:rgba(255,255,255,.18)}
.legal{top:300px;font-size:8.5px;font-weight:500;line-height:22px}

/* header bar */
.appbar{left:0;right:0;top:68px;height:34px;background:var(--blue-deep);color:var(--white);font-size:10.5px;font-weight:500}
.appbar span{position:absolute;top:50%;transform:translate(-50%,-50%);white-space:nowrap}
.appbar svg{position:absolute;top:50%;transform:translateY(-50%)}

/* main */
.canvas-area{left:0;right:0;top:116px;height:230px;background:var(--blue-deep);border-radius:24px}
.canvas-area svg{position:absolute;left:264px;top:168px}
.btn-outline,.btn-solid{top:397px;height:38px;display:flex;align-items:center;justify-content:center;font-size:11.5px;font-weight:500}
.btn-outline{left:34px;width:128px;border:1px solid var(--blue-deep);color:var(--blue-deep)}
.btn-solid{left:166px;width:125px;background:var(--blue-deep);color:var(--white)}
.chip{height:41px;width:101px;background:var(--chip);display:flex;align-items:center;justify-content:center;gap:8px;font-size:11.5px;color:var(--ink-soft)}
.results{left:86px;top:596px;width:153px;height:35px;background:var(--cyan-bright);color:var(--white);display:flex;align-items:center;justify-content:center;font-size:12px;font-weight:500}
.desk-art{left:244px;top:628px;width:84px;height:92px;border-top-left-radius:14px;background:linear-gradient(160deg,var(--cyan-soft),var(--blue-mid))}

/* profile */
.profile-band{left:0;right:0;top:114px;height:135px;background:var(--blue-deep);border-top-left-radius:40px;border-top-right-radius:30px}
.avatar-ring{left:57px;top:36px;width:60px;height:60px;border:1.5px dashed var(--white);border-radius:50%}
.avatar{left:4px;top:4px;width:49px;height:49px;border-radius:50%;background:radial-gradient(circle at 50% 40%,#8a6a55,#3c4a3a)}
.edit-image{left:143px;top:59px;font-size:10.5px;font-weight:500;color:var(--white);display:flex;align-items:center;gap:12px}
.field{left:22px;width:284px;font-size:10.5px}
.field .icon{position:absolute;left:0;top:-6px}
.field .label{position:absolute;left:21px;top:-7px;color:var(--blue-deep);font-weight:500}
.field .value{position:absolute;right:18px;top:-7px;color:var(--ink-soft)}
.field .chev{position:absolute;right:2px;top:-6px}
.field .rule{position:absolute;left:0;right:0;height:1px;background:var(--rule)}
.link-value{right:40px;font-size:10.5px;color:var(--ink-soft)}
.add-link{right:34px;top:552px;font-size:10.5px;color:var(--blue-deep);font-weight:500;display:flex;align-items:center;gap:6px}
</style>
</head>
<body>

<!-- Sign-up screen -->
<section class="screen screen--signup">
  <div class="status">
    <span>9:41</span>
    <span style="display:flex;gap:9px;align-items:center">
      <svg width="10" height="9" viewBox="0 0 10 9"><rect x="0" y="6" width="2" height="3" fill="#222"/><rect x="3" y="4" width="2" height="5" fill="#222"/><rect x="6" y="2" width="2" height="7" fill="#222"/><rect x="9" y="0" width="1" height="9" fill="#222"/></svg>
      <svg width="14" height="10" viewBox="0 0 14 10"><path d="M1 3.5a9 9 0 0 1 12 0M3 5.8a6 6 0 0 1 8 0M5 8a3 3 0 0 1 4 0" stroke="#222" stroke-width="1.5" fill="none"/></svg>
      <svg width="20" height="10" viewBox="0 0 20 10"><rect x=".5" y=".5" width="17" height="9" rx="2" fill="none" stroke="#222"/><rect x="2" y="2" width="8" height="6" fill="#222"/><rect x="18.5" y="3" width="1.5" height="4" fill="#222"/></svg>
    </span>
  </div>
  <div class="abs brand center-x">Brivonest</div>
  <div class="abs tagline center-x">Learn letters and words</div>
  <div class="abs hero-art" role="img" aria-label="Illustration of two learners writing on a large clipboard beside a phone and stacked books"></div>
  <div class="abs signup-panel">
    <div class="abs title center-x">CREATE AN ACCOUNT</div>
    <div class="abs lead center-x">ENTER YOUR EMAIL TO SIGN UP FOR<br>THIS APP</div>
    <div class="abs email-field"><span class="value">EMAIL@MAILBOX.COM</span><span class="btn">SIGN UP</span></div>
    <div class="abs alt-login center-x"><span class="dash"></span><span>OR CONTINUE WITH QUARNIX</span><span class="mark"></span><span class="dash"></span></div>
    <div class="abs panel-rule"></div>
    <div class="abs legal center-x">BY CLICKING CONTINUE, YOU AGREE TO OUR AND TERMS OF SERVICE<br>PRIVACY POLICY</div>
  </div>
</section>

<!-- Main screen -->
<section class="screen screen--main">
  <div class="status" style="top:36px">
    <span>9:41</span>
    <span style="display:flex;gap:9px;align-items:center">
      <svg width="10" height="9" viewBox="0 0 10 9"><rect x="0" y="6" width="2" height="3" fill="#222"/><rect x="3" y="4" width="2" height="5" fill="#222"/><rect x="6" y="2" width="2" height="7" fill="#222"/><rect x="9" y="0" width="1" height="9" fill="#222"/></svg>
      <svg width="14" height="10" viewBox="0 0 14 10"><path d="M1 3.5a9 9 0 0 1 12 0M3 5.8a6 6 0 0 1 8 0M5 8a3 3 0 0 1 4 0" stroke="#222" stroke-width="1.5" fill="none"/></svg>
      <svg width="20" height="10" viewBox="0 0 20 10"><rect x=".5" y=".5" width="17" height="9" rx="2" fill="none" stroke="#222"/><rect x="2" y="2" width="8" height="6" fill="#222"/><rect x="18.5" y="3" width="1.5" height="4" fill="#222"/></svg>
    </span>
  </div>
  <header class="abs appbar">
    <svg style="left:22px" width="12" height="10" viewBox="0 0 12 10"><path d="M0 1h12M0 5h12M0 9h12" stroke="#fff" stroke-width="1.5"/></svg>
    <span style="left:154px">MAIN SCREEN</span>
    <span style="left:281px">16 POINTS</span>
  </header>
  <div class="abs canvas-area" aria-label="Drawing area">
    <svg width="40" height="44" viewBox="0 0 40 44" fill="none" stroke="#fff" stroke-width="1.6">
      <path d="M20 6C10 6 3 13 3 22s7 16 16 16c4 0 4-3 2-5s-1-5 3-5h6c5 0 8-3 8-7C38 13 30 6 20 6z"/>
      <circle cx="12" cy="18" r="2.5"/><circle cx="11" cy="27" r="2.5"/><circle cx="19" cy="13" r="2.5"/><circle cx="27" cy="15" r="2.5"/>
      <path d="M34 2l-6 18"/>
    </svg>
  </div>
  <div class="abs btn-outline">SHOW ALL WORDS</div>
  <div class="abs btn-solid">PLAY ALL WORDS</div>
  <div class="abs chip" style="left:4px;top:472px"><svg width="22" height="14" viewBox="0 0 22 14"><path d="M11 0L22 4.5 11 9 0 4.5z" fill="#0054AA"/><path d="M5 7v4c3 3 9 3 12 0V7l-6 2.5z" fill="#0054AA"/></svg>WORD 1</div>
  <div class="abs chip" style="left:113px;top:472px"><svg width="22" height="14" viewBox="0 0 22 14"><path d="M11 0L22 4.5 11 9 0 4.5z" fill="#0054AA"/><path d="M5 7v4c3 3 9 3 12 0V7l-6 2.5z" fill="#0054AA"/></svg>WORD 2</div>
  <div class="abs chip" style="left:222px;top:472px"><svg width="22" height="14" viewBox="0 0 22 14"><path d="M11 0L22 4.5 11 9 0 4.5z" fill="#0054AA"/><path d="M5 7v4c3 3 9 3 12 0V7l-6 2.5z" fill="#0054AA"/></svg>WORD 3</div>
  <div class="abs chip" style="left:58px;top:521px"><svg width="22" height="14" viewBox="0 0 22 14"><path d="M11 0L22 4.5 11 9 0 4.5z" fill="#0054AA"/><path d="M5 7v4c3 3 9 3 12 0V7l-6 2.5z" fill="#0054AA"/></svg>WORD 4</div>
  <div class="abs chip" style="left:167px;top:521px;letter-spacing:1px">•••••</div>
  <div class="abs results">SHOW ME THE RESULTS</div>
  <div class="abs desk-art" role="img" aria-label="Illustration of a learner at a desk facing a chalkboard"></div>
</section>

<!-- Profile screen -->
<section class="screen screen--profile">
  <div class="status" style="top:36px">
    <span>9:41</span>
    <span style="display:flex;gap:9px;align-items:center">
      <svg width="10" height="9" viewBox="0 0 10 9"><rect x="0" y="6" width="2" height="3" fill="#222"/><rect x="3" y="4" width="2" height="5" fill="#222"/><rect x="6" y="2" width="2" height="7" fill="#222"/><rect x="9" y="0" width="1" height="9" fill="#222"/></svg>
      <svg width="14" height="10" viewBox="0 0 14 10"><path d="M1 3.5a9 9 0 0 1 12 0M3 5.8a6 6 0 0 1 8 0M5 8a3 3 0 0 1 4 0" stroke="#222" stroke-width="1.5" fill="none"/></svg>
      <svg width="20" height="10" viewBox="0 0 20 10"><rect x=".5" y=".5" width="17" height="9" rx="2" fill="none" stroke="#222"/><rect x="2" y="2" width="8" height="6" fill="#222"/><rect x="18.5" y="3" width="1.5" height="4" fill="#222"/></svg>
    </span>
  </div>
  <header class="abs appbar">
    <svg style="left:18px" width="13" height="12" viewBox="0 0 13 12" fill="none" stroke="#fff" stroke-width="1.5"><path d="M4 1L1 4l3 3"/><path d="M1 4h7a4 4 0 0 1 0 8H5"/></svg>
    <span style="left:170px">PROFILE</span>
  </header>
  <div class="abs profile-band">
    <div class="abs avatar-ring"><div class="abs avatar" role="img" aria-label="Profile photo of the user"></div></div>
    <div class="abs edit-image">EDIT PROFILE IMAGE
      <svg width="13" height="13" viewBox="0 0 13 13" fill="none" stroke="#fff" stroke-width="1.3"><path d="M7 1.5H1.5v10h10V6"/><path d="M10.5 1l1.5 1.5L6.5 8H5V6.5z"/></svg>
    </div>
  </div>

  <div class="abs field" style="top:346px">
    <svg class="icon" width="10" height="11" viewBox="0 0 10 11"><circle cx="5" cy="3" r="2.6" fill="#333"/><path d="M0 11c0-4 2-5 5-5s5 1 5 5z" fill="#333"/></svg>
    <span class="label">NAME</span><span class="value">NORA VALE</span>
    <svg class="chev" width="6" height="10" viewBox="0 0 6 10"><path d="M1 1l4 4-4 4" stroke="#333" stroke-width="1.3" fill="none"/></svg>
    <div class="rule" style="top:14px"></div>
  </div>
  <div class="abs field" style="top:393px">
    <svg class="icon" width="10" height="11" viewBox="0 0 10 11"><circle cx="5" cy="3" r="2.6" fill="#333"/><path d="M0 11c0-4 2-5 5-5s5 1 5 5z" fill="#333"/></svg>
    <span class="label">USERNAME</span><span class="value">@USERNAME</span>
    <svg class="chev" width="6" height="10" viewBox="0 0 6 10"><path d="M1 1l4 4-4 4" stroke="#333" stroke-width="1.3" fill="none"/></svg>
    <div class="rule" style="top:9px"></div>
  </div>
  <div class="abs field" style="top:438px">
    <svg class="icon" width="11" height="9" viewBox="0 0 11 9" style="top:-4px"><rect width="11" height="9" fill="#333"/><path d="M0 0l5.5 4.5L11 0" stroke="#fff" stroke-width="1" fill="none"/></svg>
    <span class="label">EMAIL</span><span class="value">NAME@MAILBOX.COM</span>
    <svg class="chev" width="6" height="10" viewBox="0 0 6 10"><path d="M1 1l4 4-4 4" stroke="#333" stroke-width="1.3" fill="none"/></svg>
    <div class="rule" style="top:14px"></div>
  </div>
  <div class="abs field" style="top:477px">
    <svg class="icon" width="12" height="12" viewBox="0 0 12 12" fill="none" stroke="#333" stroke-width="1.3"><path d="M5 7l2-2"/><path d="M6.5 3l1-1a2.1 2.1 0 0 1 3 3l-1 1M5.5 9l-1 1a2.1 2.1 0 0 1-3-3l1-1"/></svg>
    <span class="label">LINKS</span>
  </div>
  <div class="abs link-value" style="top:470px">PLUMSITE.NET</div>
  <div class="abs link-value" style="top:498px">MYPAGE.NET</div>
  <div class="abs link-value" style="top:526px">YOURPAGE.NET</div>
  <div class="abs add-link">ADD LINK
    <svg width="11" height="11" viewBox="0 0 11 11"><circle cx="5.5" cy="5.5" r="5.5" fill="#0054AA"/><path d="M5.5 3v5M3 5.5h5" stroke="#fff" stroke-width="1.4"/></svg>
  </div>
  <div class="abs field" style="top:603px">
    <svg class="icon" width="9" height="10" viewBox="0 0 9 10" style="top:-4px"><rect width="9" height="10" fill="#333"/><path d="M2 3h5M2 5h5M2 7h3" stroke="#fff" stroke-width=".9"/></svg>
    <span class="label">BIO</span><span class="value">A DESCRIPTION OF THIS USER</span>
    <svg class="chev" width="6" height="10" viewBox="0 0 6 10"><path d="M1 1l4 4-4 4" stroke="#333" stroke-width="1.3" fill="none"/></svg>
    <div class="rule" style="top:15px"></div>
  </div>
</section>

</body>
</html>
```